UX - Need some screens design for a Skill Assessment Application

I am building an app to carry out skill assessments. Depending on how the assessment is configured, it may have one or more parts
1. Question based assessment (Multiple Choice, True False, Fill in the blanks"
2. Endorsement by two colleagues - A screen that allows user to pick colleagues based on search and shows the status of pending requests
3. A written submission - a page that explains the format of the submission and a file upload
As each assessment can be configured with or without any of the steps, the assessment UI must be such that these areas get hidden/displayed based on configuration.
Colour codes to be used can be #0e78bb and #ffffff
There will also be a start screen (instructions) and an end screen (results)
Target Market(s)
Enterprise software
Number of Pages Required
4 page

```html
<!DOCTYPE html>
<html lang="en">
<head>
<meta charset="utf-8">
<title>Skillgate – Assessments</title>
<link href="https://fonts.googleapis.com/css2?family=Inter:wght@400;500;600;700&family=Noto+Sans:wght@500;600&display=swap" rel="stylesheet">
<style>
:root{
  --brand:#0e78bb;
  --header:#0056ae;
  --card:rgba(255,255,255,0.1);
  --page:#f6f7f9;
  --white:#ffffff;
  --ink:#23262b;
  --muted:#5d636b;
  --link:#0e6fb6;
  --chip:#ebebec;
  --thead:#e8e9eb;
  --tick:#13a39a;
  --nav-dim:#b9d3ef;
}
*{box-sizing:border-box;margin:0;padding:0}
html,body{width:1200px;height:771px;overflow:hidden}
body{font-family:"Inter",sans-serif;background:var(--page);color:var(--ink);position:relative}
.hero{position:absolute;left:0;top:0;width:1200px;height:287px;background:var(--header)}
.topbar{position:absolute;left:0;top:0;width:1200px;height:43px;border-bottom:1px solid rgba(255,255,255,0.15)}
.brand{position:absolute;left:70px;top:12px;display:flex;align-items:center;gap:10px;color:var(--white);font-weight:600;font-size:14px}
.brand-dot{width:20px;height:20px;border-radius:50%;background:#5cc4ee}
.nav{position:absolute;top:14px;left:487px;display:flex;gap:20px;font-size:12.5px;color:var(--nav-dim)}
.nav a{color:inherit;text-decoration:none;position:relative}
.nav a.active{color:var(--white);font-weight:700}
.nav a.active::after{content:"";position:absolute;left:0;right:0;top:24px;height:2px;background:#2aa3e6}
.top-icons{position:absolute;right:72px;top:8px;display:flex;align-items:center;gap:14px}
.avatar{border-radius:50%;background:linear-gradient(135deg,#3b5f8c,#c9a48c)}
.avatar.sm{width:28px;height:28px}
.welcome{position:absolute;left:57px;top:71px;display:flex;align-items:center;gap:20px}
.avatar.lg{width:43px;height:43px}
.welcome small{display:block;font-size:12px;color:var(--nav-dim)}
.welcome h1{font-family:"Noto Sans",sans-serif;font-weight:600;font-size:17px;color:var(--white);margin-top:3px}
.btn-create{position:absolute;left:963px;top:75px;width:177px;height:34px;background:var(--brand);border-radius:3px;color:var(--white);font-size:11.5px;font-weight:500;display:flex;align-items:center;justify-content:center;gap:8px}
.summary-title{position:absolute;left:57px;top:140px;font-family:"Noto Sans",sans-serif;font-size:14px;color:var(--white);font-weight:500}
.cards{position:absolute;left:57px;top:171px;display:flex;gap:16px}
.card{width:259px;height:89px;background:var(--card);border-radius:4px;position:relative;color:var(--white)}
.card .ic{position:absolute;left:14px;top:14px;width:34px;height:34px;border-radius:3px;background:rgba(255,255,255,0.12);display:flex;align-items:center;justify-content:center}
.card .txt{position:absolute;left:65px;top:19px}
.card .num{font-size:17px;font-weight:700}
.card .lbl{font-size:12.5px;font-weight:500;margin-top:4px}
.card .sub{font-size:9.5px;color:#d6e5f6;margin-top:3px}
.section-title{position:absolute;left:71px;top:307px;font-family:"Noto Sans",sans-serif;font-size:17px;font-weight:600}
.tabs{position:absolute;left:71px;top:348px;display:flex;height:31px;border-radius:3px;overflow:hidden;font-size:11.5px}
.tab{padding:0 17px;display:flex;align-items:center;background:#e7e8ea;color:var(--muted)}
.tab.on{background:var(--brand);color:var(--white);width:88px}
.tab b{margin-left:4px}
.views{position:absolute;left:1075px;top:355px;display:flex;gap:17px}
.table{position:absolute;left:71px;top:393px;width:1057px}
.thead{height:34px;background:var(--thead);border-radius:4px;position:relative;font-size:9.5px;color:var(--muted);letter-spacing:.2px}
.thead span,.row span{position:absolute;top:50%;transform:translateY(-50%)}
.row{height:54px;background:var(--white);border-radius:4px;position:relative;margin-top:8px;font-size:12px;color:var(--muted)}
.row:first-of-type{margin-top:8px}
.c1{left:17px}.c2{left:145px}.c3{left:444px}.c4{left:569px}.c5{left:988px}
.row .c2{color:var(--link)}
.chips{position:absolute;left:680px;top:15px;display:flex;gap:7px}
.chip{height:24px;padding:0 9px;border-radius:12px;background:var(--chip);font-size:11px;color:var(--muted);display:flex;align-items:center;gap:7px}
.kebab{position:absolute;left:1011px;top:19px}
</style>
</head>
<body>
<header class="hero">
  <div class="topbar">
    <div class="brand"><span class="brand-dot"></span>Skillgate</div>
    <nav class="nav"><a class="active" href="#">Assessments</a><a href="#">Colleagues</a><a href="#">Results</a></nav>
    <div class="top-icons">
      <svg width="18" height="18" viewBox="0 0 24 24" fill="none" stroke="#fff" stroke-width="1.6"><path d="M6 16V11a6 6 0 0 1 12 0v5l2 2H4z"/><path d="M10 20a2 2 0 0 0 4 0"/></svg>
      <svg width="18" height="18" viewBox="0 0 24 24" fill="none" stroke="#fff" stroke-width="1.6"><circle cx="12" cy="12" r="3"/><path d="M12 2v3M12 19v3M2 12h3M19 12h3M4.9 4.9l2.1 2.1M17 17l2.1 2.1M4.9 19.1 7 17M17 7l2.1-2.1"/></svg>
      <div class="avatar sm" role="img" aria-label="User profile photo"></div>
    </div>
  </div>
  <div class="welcome">
    <div class="avatar lg" role="img" aria-label="User profile photo"></div>
    <div><small>Welcome back!</small><h1>Rina S. Hartono</h1></div>
  </div>
  <div class="btn-create">
    <svg width="13" height="13" viewBox="0 0 24 24" fill="none" stroke="#fff" stroke-width="1.8"><rect x="4" y="3" width="13" height="18" rx="1"/><path d="M8 8h5M8 12h3"/><circle cx="16" cy="16" r="3.5"/></svg>
    Create New Assessment
  </div>
  <div class="summary-title">Summary</div>
  <div class="cards">
    <div class="card"><div class="ic"><svg width="22" height="22" viewBox="0 0 24 24" fill="none" stroke="#fff" stroke-width="1.6"><rect x="4" y="3" width="13" height="18" rx="1"/><path d="M8 8h5M8 12h3M8 16h2"/><circle cx="17" cy="17" r="3.5"/><path d="m15.5 17 1 1 2-2"/></svg></div><div class="txt"><div class="num">7</div><div class="lbl">My Assessments</div><div class="sub">3 pending</div></div></div>
    <div class="card"><div class="ic"><svg width="22" height="22" viewBox="0 0 24 24" fill="none" stroke="#fff" stroke-width="1.6"><path d="m12 2 1.5 3 3 .4-2.2 2 .6 3-2.9-1.5-2.9 1.5.6-3-2.2-2 3-.4z"/><path d="M3 14h3v7H3zM6 15h5l3 2h4l2 2-4 2H6"/></svg></div><div class="txt"><div class="num">3</div><div class="lbl">Endorsements</div><div class="sub">1 pending</div></div></div>
    <div class="card"><div class="ic"><svg width="22" height="22" viewBox="0 0 24 24" fill="none" stroke="#fff" stroke-width="1.6"><circle cx="7" cy="6" r="2.5"/><circle cx="17" cy="6" r="2.5"/><circle cx="12" cy="12" r="2.5"/><path d="M3 14a4 4 0 0 1 5-3M21 14a4 4 0 0 0-5-3M8 21a4 4 0 0 1 8 0"/></svg></div><div class="txt"><div class="num">10</div><div class="lbl">Colleagues</div><div class="sub">Last updated on May 23, 2024</div></div></div>
    <div class="card"><div class="ic"><svg width="22" height="22" viewBox="0 0 24 24" fill="none" stroke="#fff" stroke-width="1.6"><path d="M12 3v11M8 7l4-4 4 4M4 13v6h16v-6"/></svg></div><div class="txt"><div class="num">7</div><div class="lbl">Submissions</div><div class="sub">Last submit on May 23, 2024</div></div></div>
  </div>
</header>

<h2 class="section-title">Assessments</h2>
<div class="tabs"><div class="tab on">Pending<b>3</b></div><div class="tab">Completed<b>4</b></div></div>
<div class="views">
  <svg width="18" height="17" viewBox="0 0 18 17" fill="none" stroke="#8a9099" stroke-width="1.3"><path d="M5 2h13M5 8.5h13M5 15h13M0 2h2M0 8.5h2M0 15h2"/></svg>
  <svg width="17" height="17" viewBox="0 0 17 17" fill="none" stroke="#0e78bb" stroke-width="1.6"><rect x="1" y="1" width="6" height="6"/><rect x="10" y="1" width="6" height="6"/><rect x="1" y="10" width="6" height="6"/><rect x="10" y="10" width="6" height="6"/></svg>
</div>

<section class="table">
  <div class="thead"><span class="c1">ASSESSMENT ID</span><span class="c2">ASSESSMENT TITLE</span><span class="c3">PUBLISHED ON</span><span class="c4">DUE DATE</span><span class="c5">ACTIONS</span></div>
  <div class="row"><span class="c1">1723091983</span><span class="c2">Application Design Capabilities</span><span class="c3">20/05/2024</span><span class="c4">24/05/2024</span>
    <div class="chips"><div class="chip">Quiz</div><div class="chip">Endorsement</div><div class="chip">Submission</div></div>
    <svg class="kebab" width="4" height="16" viewBox="0 0 4 16" fill="#3b3f45"><circle cx="2" cy="2" r="1.6"/><circle cx="2" cy="8" r="1.6"/><circle cx="2" cy="14" r="1.6"/></svg></div>
  <div class="row"><span class="c1">2317091983</span><span class="c2">UI/UX Designer</span><span class="c3">20/05/2024</span><span class="c4">24/05/2024</span>
    <div class="chips"><div class="chip">Quiz<svg width="14" height="14" viewBox="0 0 14 14"><circle cx="7" cy="7" r="7" fill="#13a39a"/><path d="m4 7 2 2 4-4" fill="none" stroke="#fff" stroke-width="1.4"/></svg></div><div class="chip">Endorsement</div></div>
    <svg class="kebab" width="4" height="16" viewBox="0 0 4 16" fill="#3b3f45"><circle cx="2" cy="2" r="1.6"/><circle cx="2" cy="8" r="1.6"/><circle cx="2" cy="14" r="1.6"/></svg></div>
  <div class="row"><span class="c1">1983172309</span><span class="c2">Sales Representative</span><span class="c3">20/05/2024</span><span class="c4">24/05/2024</span>
    <div class="chips"><div class="chip">Quiz<svg width="14" height="14" viewBox="0 0 14 14"><circle cx="7" cy="7" r="7" fill="#13a39a"/><path d="m4 7 2 2 4-4" fill="none" stroke="#fff" stroke-width="1.4"/></svg></div><div class="chip">Endorsement<svg width="14" height="14" viewBox="0 0 14 14"><circle cx="7" cy="7" r="7" fill="#13a39a"/><path d="m4 7 2 2 4-4" fill="none" stroke="#fff" stroke-width="1.4"/></svg></div><div class="chip">Submission</div></div>
    <svg class="kebab" width="4" height="16" viewBox="0 0 4 16" fill="#3b3f45"><circle cx="2" cy="2" r="1.6"/><circle cx="2" cy="8" r="1.6"/><circle cx="2" cy="14" r="1.6"/></svg></div>
</section>
</body>
</html>
```